Business cards to launch an education platform

Hi,
I am looking at having new business cards designed.
I am a startup, developing a web platform for schools and university, the education world. It's an online assessment system.
I would like a card that looks classy, and that is using the colors and the font of my logo.

I have attached:
1) my logo
2) A business card that I have designed quickly so you can have all the information required in the card, but I really don't like it.
3) The font that I am using (Lato Regular) to design my web platform
4) Some screenshots of my web platform so you can have a look at the style that I have.

Target Market(s)

Major market: Education system: Schools and university
Minor markets: Business in general

Industry/Entity Type

Business

Contact Information for Business Card

Clara Fenwick
Director

M: 0437 518 902
E: clara.fenwick@amberLoomSystems.com.au

Requirements
Must have
• The colors of my logo

```html
<!DOCTYPE html>
<html lang="en">
<head>
<meta charset="UTF-8">
<title>Amber Loom Systems – Business Cards</title>
<link rel="stylesheet" href="https://fonts.googleapis.com/css2?family=Lato:wght@300;400;700&display=swap">
<style>
  :root {
    --bg: #e9ecef;
    --card-white: #ffffff;
    --card-grey: #f1f2f4;
    --brand-blue: #1f6fb2;
    --brand-cyan: #2bb0dc;
    --brand-deep: #0d4f8a;
    --text-dark: #1d4f86;
    --text-soft: #2a8fc9;
    --line: #2bb0dc;
  }
  * { margin: 0; padding: 0; box-sizing: border-box; }
  html, body {
    width: 1200px; height: 780px; overflow: hidden;
    background: var(--bg);
    font-family: "Lato", sans-serif;
  }
  .sheet {
    position: relative; width: 1200px; height: 780px;
    display: flex; align-items: center; justify-content: center; gap: 40px;
  }
  .card {
    position: relative; width: 540px; height: 330px;
    border-radius: 22px; overflow: hidden;
    box-shadow: 0 10px 26px rgba(0,0,0,0.16);
  }
  /* Front */
  .card--front {
    background: radial-gradient(ellipse at 45% 40%, var(--card-white) 0%, var(--card-grey) 100%);
  }
  .brand {
    position: absolute; display: flex; align-items: center; gap: 14px;
  }
  .brand__square {
    width: 52px; height: 52px; background: var(--brand-blue); flex: none;
  }
  .brand__name {
    font-weight: 400; color: var(--brand-blue); line-height: 1.05;
    text-transform: uppercase;
  }
  .brand__name span { display: block; }
  .card--front .brand { left: 42px; top: 84px; }
  .card--front .brand__name { font-size: 27px; letter-spacing: 3px; }
  .card--front .brand__name span + span { font-size: 19px; letter-spacing: 4px; }

  .holder {
    position: absolute; right: 46px; top: 150px; text-align: left;
  }
  .holder__name { font-size: 22px; font-weight: 400; color: var(--text-dark); }
  .holder__role { font-size: 13px; font-weight: 300; color: var(--text-soft); margin-left: 70px; margin-top: -2px; }
  .rule {
    position: absolute; left: 44px; right: 128px; top: 182px;
    height: 1.5px; background: var(--line);
  }
  .contact {
    position: absolute; left: 150px; bottom: 40px;
    font-size: 13px; color: var(--text-dark); font-weight: 400;
  }
  .contact__row { display: flex; align-items: center; gap: 8px; margin-top: 6px; }
  .contact__icon {
    width: 14px; height: 14px; background: var(--text-soft); border-radius: 2px;
    display: flex; align-items: center; justify-content: center; flex: none;
  }
  /* Back */
  .card--back {
    background: radial-gradient(ellipse at 50% 45%, #35bfe2 0%, #1b8fcc 45%, var(--brand-deep) 100%);
  }
  .card--back .brand { left: 50%; top: 50%; transform: translate(-50%, -50%); }
  .card--back .brand__square { background: #ffffff; width: 60px; height: 60px; }
  .card--back .brand__name { color: #ffffff; font-size: 31px; letter-spacing: 4px; }
  .card--back .brand__name span + span { font-size: 21px; letter-spacing: 5px; }
</style>
</head>
<body>
  <main class="sheet">
    <section class="card card--front" aria-label="Business card front">
      <div class="brand">
        <div class="brand__square"></div>
        <div class="brand__name"><span>Amber Loom</span><span>Systems</span></div>
      </div>
      <div class="holder">
        <div class="holder__name">Clara Fenwick</div>
        <div class="holder__role">Director</div>
      </div>
      <div class="rule"></div>
      <div class="contact">
        <div class="contact__row">
          <span class="contact__icon">
            <svg width="10" height="10" viewBox="0 0 10 10"><rect x="2.5" y="0.8" width="5" height="8.4" rx="1" fill="none" stroke="#fff" stroke-width="1.1"/></svg>
          </span>
          0437 518 902
        </div>
        <div class="contact__row">
          <span class="contact__icon">
            <svg width="10" height="10" viewBox="0 0 10 10"><rect x="0.8" y="2" width="8.4" height="6" fill="none" stroke="#fff" stroke-width="1"/><path d="M0.8 2 L5 5.5 L9.2 2" fill="none" stroke="#fff" stroke-width="1"/></svg>
          </span>
          clara.fenwick@amberLoomSystems.com.au
        </div>
      </div>
    </section>

    <section class="card card--back" aria-label="Business card back">
      <div class="brand">
        <div class="brand__square"></div>
        <div class="brand__name"><span>Amber Loom</span><span>Systems</span></div>
      </div>
    </section>
  </main>
</body>
</html>
```